Basic business card

use my newly created logo - and the phrases (Leaner Test Budgets & Faster Path from Design to Market) - and my new email domain / ID - use at conferences / tradeshows

Industry/Entity Type

semiconductor

Contact Information for Business Card

Daniel K Forde, Owner, communicate via Logo - Lower COT - Cost of Test, Accelerated NPI - New Product Introduction, phone +1 555 613 0946, Brookvale, Oregon, USA, daniel.forde@qal-vub.com

Font styles to use
Sans Serif

Requirements
Nice to have
• re-use my logo created via Pixel Harbor last August (#7315926)

```html
<!DOCTYPE html>
<html lang="en">
<head>
<meta charset="utf-8">
<title>QAL-VUB Business Card</title>
<link rel="stylesheet" href="https://fonts.googleapis.com/css2?family=Montserrat:wght@400;500;700&display=swap">
<style>
  :root {
    --backdrop: #d3d7d8;
    --paper: #ffffff;
    --ink-navy: #1c2440;
    --edge-blue: #1d4fa8;
    --tagline-blue: #2f72c4;
    --ink-grey: #3a3d46;
    --accent-orange: #e07a1f;
    --accent-blue: #1d55a0;
    --accent-green: #5a9e2a;
  }
  html, body {
    margin: 0;
    width: 1200px;
    height: 829px;
    overflow: hidden;
    background: var(--backdrop);
    font-family: "Montserrat", sans-serif;
  }
  .stage {
    position: relative;
    width: 1200px;
    height: 829px;
    display: flex;
    align-items: center;
    justify-content: center;
    gap: 48px;
  }
  .card {
    position: relative;
    width: 525px;
    height: 300px;
    background: var(--paper);
    border-bottom: 4px solid var(--edge-blue);
    box-shadow: 0 10px 24px rgba(0, 0, 0, 0.12);
    box-sizing: border-box;
  }
  .card-front { padding: 40px 44px; }
  .wordmark {
    font-family: "Montserrat", sans-serif;
    font-weight: 500;
    color: var(--ink-navy);
    letter-spacing: 0.04em;
    margin: 0;
  }
  .card-front .wordmark { font-size: 44px; line-height: 1; }
  .person { margin-top: 26px; }
  .person-name {
    font-weight: 700;
    font-size: 19px;
    color: var(--ink-navy);
    margin: 0;
  }
  .person-role {
    font-size: 13px;
    color: var(--ink-grey);
    margin: 2px 0 0;
  }
  .contact-list {
    list-style: none;
    padding: 0;
    margin: 18px 0 0;
    font-size: 13px;
    color: var(--ink-grey);
    line-height: 1.75;
  }
  .contact-list li { display: flex; align-items: center; gap: 8px; }
  .contact-icon { width: 12px; height: 12px; flex: none; }
  .card-back {
    display: flex;
    flex-direction: column;
    align-items: center;
    justify-content: center;
    padding: 0 28px;
  }
  .brand-lockup { display: flex; align-items: center; gap: 14px; }
  .brand-square {
    width: 34px;
    height: 34px;
    background: var(--ink-navy);
  }
  .card-back .wordmark { font-size: 52px; line-height: 1; }
  .tagline {
    margin: 30px 0 0;
    font-size: 12.5px;
    color: var(--tagline-blue);
    letter-spacing: 0.04em;
    text-align: center;
    white-space: nowrap;
  }
</style>
</head>
<body>
<main class="stage">
  <section class="card card-front" aria-label="Card front with contact details">
    <h1 class="wordmark">QAL-VUB</h1>
    <div class="person">
      <p class="person-name">Daniel K Forde</p>
      <p class="person-role">Owner</p>
    </div>
    <ul class="contact-list">
      <li>
        <svg class="contact-icon" viewBox="0 0 12 12" aria-hidden="true">
          <path d="M1 4 Q6 0 11 4 L9.5 5.5 L8 4.5 L4 4.5 L2.5 5.5 Z M3 6 H9 L10 11 H2 Z" fill="var(--accent-orange)"/>
        </svg>
        +1 555 613 0946
      </li>
      <li>
        <svg class="contact-icon" viewBox="0 0 12 12" aria-hidden="true">
          <rect x="0.5" y="2" width="11" height="8" fill="var(--accent-blue)"/>
          <path d="M0.5 2 L6 6.5 L11.5 2 M0.5 10 L4.5 5.5 M11.5 10 L7.5 5.5" stroke="#fff" stroke-width="1" fill="none"/>
        </svg>
        daniel.forde@qal-vub.com
      </li>
      <li>
        <svg class="contact-icon" viewBox="0 0 12 12" aria-hidden="true">
          <path d="M6 11.5 C3 7.5 2 6 2 4.5 A4 4 0 0 1 10 4.5 C10 6 9 7.5 6 11.5 Z" fill="var(--accent-green)"/>
          <circle cx="6" cy="4.5" r="1.5" fill="#fff"/>
        </svg>
        Brookvale, Oregon, USA
      </li>
    </ul>
  </section>

  <section class="card card-back" aria-label="Card back with brand and tagline">
    <div class="brand-lockup">
      <span class="brand-square" aria-hidden="true"></span>
      <h2 class="wordmark">QAL-VUB</h2>
    </div>
    <p class="tagline">Leaner Test Budgets &amp; Faster Path from Design to Market</p>
  </section>
</main>
</body>
</html>
```